Automotive Accessories Business Card

Design a business template that match our new logo design and our industry.

https://www.qelmotorgear.com/

Target Market(s)

Aftermarket auto parts and accessories

Industry/Entity Type

automotive

Contact Information for Business Card

company logo

Font styles to use
Serif
Sans Serif

Colors
EB3D1F
EC4F4E
F09395
F8D3D4
FCEDEE

```html
<!DOCTYPE html>
<html lang="en">
<head>
<meta charset="utf-8">
<title>QEL Motor Gear – Business Card</title>
<link href="https://fonts.googleapis.com/css2?family=Poppins:wght@400;600;700&display=swap" rel="stylesheet">
<style>
  :root {
    --brand-red: #d92027;
    --charcoal: #404042;
    --ink: #1d1d1f;
    --paper: #ffffff;
    --backdrop: #ecebea;
  }
  * { margin: 0; padding: 0; box-sizing: border-box; }
  html, body { width: 1200px; height: 900px; overflow: hidden; }
  body {
    background: var(--backdrop);
    font-family: "Poppins", sans-serif;
    position: relative;
  }
  .card {
    position: absolute;
    left: 250px;
    width: 700px;
    height: 400px;
    overflow: hidden;
    box-shadow: 0 6px 18px rgba(0,0,0,0.18);
  }
  .card--back { top: 40px; background: var(--brand-red); }
  .card--front { top: 460px; background: var(--paper); }

  .wordmark {
    font-family: "Poppins", sans-serif;
    font-weight: 700;
    letter-spacing: 0.02em;
    text-transform: uppercase;
    display: flex;
    align-items: center;
    gap: 12px;
    white-space: nowrap;
  }
  .wordmark__square { display: block; }
  .card--back .wordmark {
    position: absolute;
    left: 50%; top: 50%;
    transform: translate(-50%, -50%);
    color: var(--paper);
    font-size: 50px;
  }
  .card--back .wordmark__square { width: 30px; height: 30px; background: var(--paper); }
  .card--front .wordmark {
    position: absolute;
    right: 40px; top: 62px;
    color: var(--brand-red);
    font-size: 28px;
  }
  .card--front .wordmark__square { width: 18px; height: 18px; background: var(--charcoal); }

  .person { position: absolute; left: 48px; top: 58px; }
  .person__name {
    color: var(--brand-red);
    font-weight: 600;
    font-size: 27px;
    line-height: 1.05;
    text-transform: uppercase;
  }
  .person__role { color: var(--ink); font-size: 17px; line-height: 1.3; }

  .contact { position: absolute; left: 82px; top: 160px; color: var(--ink); font-size: 17px; line-height: 1.45; }
  .contact__row { display: flex; align-items: center; gap: 10px; }
  .contact__icon { width: 20px; height: 20px; flex: none; }
  .contact__address { margin-top: 14px; }

  .wave { position: absolute; inset: 0; width: 700px; height: 400px; }
  .website {
    position: absolute;
    right: 40px; bottom: 30px;
    color: var(--paper);
    font-size: 17px;
  }
</style>
</head>
<body>

<section class="card card--back" aria-label="Card back">
  <div class="wordmark"><span class="wordmark__square"></span>QEL Motor Gear</div>
</section>

<section class="card card--front" aria-label="Card front">
  <svg class="wave" viewBox="0 0 700 400" aria-hidden="true">
    <path d="M0,342 C240,342 450,300 700,198 L700,400 L0,400 Z" fill="var(--brand-red)"/>
    <path d="M0,312 C220,312 400,290 540,226 C420,300 240,334 0,334 Z" fill="var(--charcoal)"/>
  </svg>

  <div class="person">
    <div class="person__name">Marcus Ellery</div>
    <div class="person__role">Managing Director</div>
  </div>

  <div class="wordmark"><span class="wordmark__square"></span>QEL Motor Gear</div>

  <div class="contact">
    <div class="contact__row">
      <svg class="contact__icon" viewBox="0 0 24 24" aria-hidden="true">
        <path d="M6.6 10.8a15 15 0 0 0 6.6 6.6l2.2-2.2a1 1 0 0 1 1-.25 11.4 11.4 0 0 0 3.6.57 1 1 0 0 1 1 1V20a1 1 0 0 1-1 1A17 17 0 0 1 3 4a1 1 0 0 1 1-1h3.5a1 1 0 0 1 1 1c0 1.25.2 2.45.57 3.57a1 1 0 0 1-.25 1z" fill="var(--brand-red)"/>
      </svg>
      <span>055-318 742 260</span>
    </div>
    <div class="contact__row">
      <svg class="contact__icon" viewBox="0 0 24 24" aria-hidden="true">
        <rect x="2" y="5" width="20" height="14" fill="var(--brand-red)"/>
        <path d="M2 5l10 8 10-8" fill="none" stroke="var(--paper)" stroke-width="1.6"/>
      </svg>
      <span>info@qelmotorgear.com</span>
    </div>
    <div class="contact__address">421, Address line here<br>Country Name, 45452</div>
  </div>

  <div class="website">www.qelmotorgear.com</div>
</section>

</body>
</html>
```